Harborview Estates Business Card for Apartment Buildings

Create business cards for resident managers who run apartment buildings. The audience is the public who are searching for apartment rentals, and current residents who live at the apartment building. Key design element will be incorporating the company logo, however, the logo cannot dominate. The building name and manager name are more important than the logo. Current business card design leaves little room for copy, so we may need to reduce the size on the current card to allow for more space for copy.

Target Market(s)

Adults 18-65 years of age, who are looking for an apartment rental, plus current residents who live at our apartment buildings.

Industry/Entity Type

Property Management

Contact Information for Business Card

A major design element will be use of the company logo. Important property and manager contact information must be part of the design. The size of the logo will need to be reduced to make room for building and manager contact copy.

Font styles to use
Sans Serif

Colors
3176b5
000000
959595
ffffff

Requirements
Must have
• 1) Incorporate the company logo.
• 2) Use the company colors (dark blue, black/grey, over white).
• 3) FEATURE THE BUILDING NAME
• 4) FEATURE THE MANAGER NAME
• 5) The company name is less important than BUILDING and MANAGER
• 6) Manager contact information
• **SEE ATTACHED CREATIVE BRIEF**
Nice to have
• 1) Back of card logo watermark
• 2) Ability to write notes on back of carfd
Should not have
• Avoid letting the company logo dominate the card, the building name and manager are more important than the company logo.

```html
<!DOCTYPE html>
<html lang="en">
<head>
<meta charset="UTF-8">
<title>Harborview Estates – Resident Manager Card</title>
<link href="https://fonts.googleapis.com/css2?family=Lato:wght@400;700&family=Oswald:wght@500&display=swap" rel="stylesheet">
<style>
  :root {
    --brand-blue: #1a6fb3;
    --brand-blue-light: #3176b5;
    --ink: #2b2b2b;
    --grey: #959595;
    --paper: #ffffff;
    --backdrop: #e9ebee;
  }
  * { box-sizing: border-box; margin: 0; padding: 0; }
  html, body { width: 1200px; height: 900px; overflow: hidden; }
  body { background: var(--backdrop); font-family: "Lato", sans-serif; position: relative; }

  .card {
    position: absolute;
    width: 680px;
    height: 388px;
    border-radius: 18px;
    overflow: hidden;
    box-shadow: 0 6px 18px rgba(0,0,0,0.12);
  }

  /* Back of card */
  .card-back { left: 330px; top: 36px; background: var(--brand-blue); color: var(--paper); }
  .card-back .watermark {
    position: absolute; left: 300px; top: 20px; width: 340px; height: 340px;
    border-radius: 50%; border: 10px solid rgba(255,255,255,0.10);
  }
  .card-back .wordmark {
    position: absolute; left: 0; right: 0; top: 130px; text-align: center;
    display: flex; align-items: center; justify-content: center; gap: 18px;
  }
  .wordmark-square { width: 44px; height: 44px; background: currentColor; }
  .card-back .wordmark-text {
    font-weight: 700; font-size: 46px; letter-spacing: 1px; text-transform: uppercase; line-height: 1;
  }
  .card-back .website {
    position: absolute; left: 0; right: 0; bottom: 44px; text-align: center;
    font-size: 18px; letter-spacing: 1.5px;
  }

  /* Front of card */
  .card-front { left: 190px; top: 474px; background: var(--paper); color: var(--ink); }
  .card-front .watermark {
    position: absolute; left: 400px; top: 110px; width: 380px; height: 380px;
    border-radius: 50%; border: 10px solid rgba(149,149,149,0.10);
  }
  .card-front .base-band {
    position: absolute; left: 0; right: 0; bottom: 0; height: 16px; background: var(--brand-blue);
  }
  .card-front .wordmark {
    position: absolute; left: 34px; top: 42px; display: flex; align-items: center; gap: 12px;
    color: var(--brand-blue);
  }
  .card-front .wordmark-square { width: 30px; height: 30px; }
  .card-front .wordmark-text { font-weight: 700; font-size: 28px; text-transform: uppercase; letter-spacing: 0.5px; }

  .manager { position: absolute; left: 34px; top: 128px; }
  .manager-name {
    font-family: "Oswald", sans-serif; font-weight: 500; font-size: 38px;
    color: var(--brand-blue); text-transform: uppercase; line-height: 1.05;
  }
  .manager-title { font-size: 19px; color: #444; margin-top: 2px; }

  .contact-list { position: absolute; list-style: none; font-size: 21px; color: #333; }
  .contact-list li { display: flex; align-items: center; gap: 14px; height: 30px; }
  .contact-list svg { width: 16px; height: 16px; fill: none; stroke: var(--brand-blue); stroke-width: 1.8; flex: none; }
  .phones { left: 34px; top: 262px; }
  .online { left: 390px; top: 296px; font-size: 20px; }

  .property { position: absolute; left: 390px; top: 170px; }
  .property-name { font-weight: 700; font-size: 24px; color: var(--brand-blue); }
  .property-address { font-size: 20px; color: #333; line-height: 1.3; margin-top: 2px; }
</style>
</head>
<body>

<section class="card card-back" aria-label="Back of business card">
  <div class="watermark"></div>
  <div class="wordmark">
    <span class="wordmark-square"></span>
    <span class="wordmark-text">Harborview Estates</span>
  </div>
  <p class="website">www.harborviewest.com</p>
</section>

<section class="card card-front" aria-label="Front of business card">
  <div class="watermark"></div>

  <div class="wordmark">
    <span class="wordmark-square"></span>
    <span class="wordmark-text">Harborview Estates</span>
  </div>

  <div class="manager">
    <h1 class="manager-name">Marisol Delgado</h1>
    <p class="manager-title">Resident Manager</p>
  </div>

  <ul class="contact-list phones">
    <li>
      <svg viewBox="0 0 16 16"><path d="M4 1.5 L6 5 L4.5 6.5 Q6 9.8 9.5 11.5 L11 10 L14.5 12 L13 14.5 Q6 14 1.5 3 Z"/></svg>
      555-201-4470
    </li>
    <li>
      <svg viewBox="0 0 16 16"><rect x="4" y="1.5" width="8" height="4"/><rect x="1.5" y="5.5" width="13" height="6" rx="1"/><rect x="4" y="9.5" width="8" height="5"/></svg>
      555-201-4471
    </li>
    <li>
      <svg viewBox="0 0 16 16"><rect x="4" y="1" width="8" height="14" rx="1.5"/><line x1="7" y1="12.5" x2="9" y2="12.5"/></svg>
      555-388-9025
    </li>
  </ul>

  <div class="property">
    <h2 class="property-name">Cedar Court Apartments</h2>
    <p class="property-address">1480 Linden Avenue<br>Bayport, CA 90417</p>
  </div>

  <ul class="contact-list online">
    <li>
      <svg viewBox="0 0 16 16"><rect x="1.5" y="3.5" width="13" height="9"/><path d="M1.5 3.5 L8 9 L14.5 3.5"/></svg>
      marisol@harborviewest.com
    </li>
    <li>
      <svg viewBox="0 0 16 16"><circle cx="8" cy="8" r="6.5"/><ellipse cx="8" cy="8" rx="3" ry="6.5"/><line x1="1.5" y1="8" x2="14.5" y2="8"/></svg>
      www.harborviewest.com
    </li>
  </ul>

  <div class="base-band"></div>
</section>

</body>
</html>
```